Tri-fold flyer for our high quality fast-food concept

This is a project for a tri-fold flyer with the presentation and menu of our new takeaway and delivery high quality fast-food concept.

The whole flyer should look modern and high quality.

The vegetarian options should be notified by a little sign, like a leave for example.
Vegetarian options are:
Authentic, Veggie, Cheese, Malvenne, Tessala, Rima Dubel, Pelvo, Mursgrave, Vestal, Quelvira, Bellucave, Tarvik, Verte, Fries, Focaccia

The most specific products in our menu are the burgers, gnocchi and piozzas, if it is possible to slightly put in evidence these sections.

It would be nice if you could reuse the peppers of our logo in a subtle way.

In attachment are:
- a draft for the flyer indicating the position of each section, with the contents (dishes with ingredients and prices). PDF shows how it should look like, DOC might easier me to read the contents
- the logo which should be used at least in the front page
- some pictures of our dishes. One picture for each section would probably be nice.
- the QR Code on the back page (see yellow text)
- 2 pictures of the packaging as we use environmentally friendly ones (see yellow the in the back page).

Please note that this is a long term partnership, as we will work again with the winner when we will need to make small changes to our menu, so we hope you will provide us with a lovely and professional design :-)

Besoin de plus de jours pour examiner

Target Market(s)

Local people between 25-45

Industry/Entity Type

Fast food

Requirements
Must have
• It is much better if you could use the colors of our logo, to create a whole atmosphere
Nice to have
• Agood balance between bright and dark - Though there is much content, the text should not be too small

```html
<!DOCTYPE html>
<html lang="en">
<head>
<meta charset="utf-8">
<title>Ember Bun Co – Trifold Brochure</title>
<link href="https://fonts.googleapis.com/css2?family=Oswald:wght@400;500;600&family=Alfa+Slab+One&display=swap" rel="stylesheet">
<style>
  :root{
    --bg:#fdf0d6;
    --paper:#f6b53c;
    --paper-light:#f8c25a;
    --paper-dark:#eea82e;
    --ink:#3a1d0c;
    --ink-soft:#5a3316;
    --red:#d6262d;
    --white:#ffffff;
    --photo-a:rgba(196,108,40,.38);
    --photo-b:rgba(214,58,40,.28);
  }
  *{box-sizing:border-box;margin:0;padding:0}
  html,body{width:1200px;height:600px;overflow:hidden;background:var(--bg)}
  body{position:relative;font-family:"Oswald",sans-serif;color:var(--ink)}

  .showcase-title{position:absolute;left:0;width:1200px;text-align:center;font-weight:500;color:#1f1208;line-height:1}
  .showcase-title--main{top:60px;font-size:21px;letter-spacing:.2px}
  .showcase-title--sub{top:87px;font-size:15px;font-weight:400}

  .brochure{position:absolute;top:143px;width:507px;height:355px;display:flex;box-shadow:0 22px 18px -14px rgba(60,35,10,.35)}
  .brochure--outside{left:70px}
  .brochure--inside{left:624px}
  .panel{position:relative;flex:1;height:100%;overflow:hidden;background:linear-gradient(180deg,var(--paper-light),var(--paper))}
  .panel--fold-a{background:linear-gradient(90deg,var(--paper) 0%,var(--paper-light) 100%)}
  .panel--fold-b{background:linear-gradient(90deg,var(--paper-dark) 0%,var(--paper) 100%)}

  .menu-heading{position:absolute;font-size:9.5px;font-weight:600;letter-spacing:2.2px;color:var(--ink)}
  .menu-list{position:absolute;list-style:none;width:130px}
  .menu-list li{display:flex;align-items:flex-end;height:15.6px;font-size:4.6px;text-transform:uppercase;color:var(--ink-soft)}
  .menu-list .item-name{width:68px;white-space:nowrap;overflow:hidden}
  .menu-list .item-dots{width:40px;border-bottom:.6px dotted var(--ink-soft);margin-bottom:1px}
  .menu-list .item-price{margin-left:5px}

  .photo{position:absolute;border-radius:4px;background:linear-gradient(160deg,var(--photo-a),var(--photo-b))}

  .brand{position:absolute;left:43px;top:22px;display:flex;align-items:center;gap:6px;font-size:10.5px;font-weight:500;color:var(--ink)}
  .brand-dot{width:13px;height:13px;border-radius:50%;background:var(--ink)}
  .tagline{position:absolute;left:35px;top:62px;width:92px;border:.6px dashed var(--ink);padding:1.5px 0;text-align:center;font-size:3.8px;text-transform:uppercase;white-space:nowrap}
  .promo-title{position:absolute;left:0;width:100%;text-align:center;font-family:"Alfa Slab One",serif;color:var(--ink);line-height:1}
  .promo-title--big{top:78px;font-size:23px}
  .promo-title--small{top:104px;font-size:12px}
  .price-badge{position:absolute;left:17px;top:203px;width:48px;height:48px;border-radius:50%;background:var(--red);border:1.5px dashed rgba(255,255,255,.7);color:var(--white);text-align:center;padding-top:9px}
  .price-badge .amount{font-size:15px;font-weight:600;line-height:1}
  .price-badge .amount small{font-size:7px}
  .price-badge .only{font-size:6px;letter-spacing:2px}
  .spicy-tag{position:absolute;left:60px;top:284px;background:var(--ink);color:var(--white);font-size:6.5px;letter-spacing:1px;padding:1.5px 6px}
  .delivery{position:absolute;left:42px;top:304px;width:128px;height:31px;background:var(--red);clip-path:polygon(0 0,100% 0,100% 100%,0 100%,8% 50%);color:var(--white);display:flex;align-items:center;padding-left:18px;gap:6px}
  .delivery-text{line-height:1.05}
  .delivery-text .label{font-size:6.5px}
  .delivery-text .phone{font-size:10px;font-weight:500}

  .contact{position:absolute;left:0;width:100%;text-align:center;font-size:5.8px;letter-spacing:.8px;text-transform:uppercase;color:var(--ink);white-space:nowrap}
  .contact--web{top:291px}
  .contact--address{top:304px}
  .social-row{position:absolute;top:328px;left:0;width:100%;display:flex;justify-content:center;gap:6px}
  .social-row span{width:10px;height:10px;border-radius:50%;background:var(--ink)}

  .offer-title{position:absolute;left:22px;top:160px;font-size:13px;font-weight:600;letter-spacing:2.6px}
  .offer-hours{position:absolute;left:22px;top:181px;width:107px;height:16px;background:var(--ink);color:var(--paper-light);font-size:7.5px;letter-spacing:2.4px;display:flex;align-items:center;justify-content:center}
  .offer-discount{position:absolute;left:22px;top:200px;font-size:24px;font-weight:600;letter-spacing:4px;line-height:1}
</style>
</head>
<body>

<h1 class="showcase-title showcase-title--main">TRIFOLD BROCHURE</h1>
<p class="showcase-title showcase-title--sub">AMERICAN FOOD</p>

<!-- Outside spread -->
<section class="brochure brochure--outside">
  <div class="panel panel--fold-a">
    <h2 class="menu-heading" style="left:22px;top:24px">DESSERTS</h2>
    <ol class="menu-list" style="left:22px;top:42px">
      <li><span class="item-name">Lorem ipsum dolor</span><span class="item-dots"></span><span class="item-price">$10</span></li>
      <li><span class="item-name">Duis aute irure</span><span class="item-dots"></span><span class="item-price">$10</span></li>
      <li><span class="item-name">Excepteur sint occaecat</span><span class="item-dots"></span><span class="item-price">$10</span></li>
      <li><span class="item-name">Consectetur adipiscing elit</span><span class="item-dots"></span><span class="item-price">$10</span></li>
      <li><span class="item-name">Reprehenderit in voluptate</span><span class="item-dots"></span><span class="item-price">$10</span></li>
      <li><span class="item-name">Nostrud exercitation</span><span class="item-dots"></span><span class="item-price">$10</span></li>
      <li><span class="item-name">Ut enim</span><span class="item-dots"></span><span class="item-price">$10</span></li>
      <li><span class="item-name">Spinach artichoke dip</span><span class="item-dots"></span><span class="item-price">$10</span></li>
    </ol>
    <div class="photo" role="img" aria-label="Photo of ketchup, fries in a red carton and a sesame burger" style="left:22px;top:178px;width:150px;height:177px;border-radius:4px 4px 0 0"></div>
  </div>

  <div class="panel panel--fold-b">
    <h2 class="menu-heading" style="left:20px;top:24px">DRINKS</h2>
    <ol class="menu-list" style="left:20px;top:42px">
      <li><span class="item-name">Lorem ipsum dolor</span><span class="item-dots"></span><span class="item-price">$10</span></li>
      <li><span class="item-name">Duis aute irure</span><span class="item-dots"></span><span class="item-price">$10</span></li>
      <li><span class="item-name">Excepteur sint occaecat</span><span class="item-dots"></span><span class="item-price">$10</span></li>
      <li><span class="item-name">Consectetur adipiscing elit</span><span class="item-dots"></span><span class="item-price">$10</span></li>
      <li><span class="item-name">Reprehenderit in voluptate</span><span class="item-dots"></span><span class="item-price">$10</span></li>
      <li><span class="item-name">Nostrud exercitation</span><span class="item-dots"></span><span class="item-price">$10</span></li>
      <li><span class="item-name">Ut enim</span><span class="item-dots"></span><span class="item-price">$10</span></li>
      <li><span class="item-name">Spinach artichoke dip</span><span class="item-dots"></span><span class="item-price">$10</span></li>
    </ol>
    <div class="photo" role="img" aria-label="Photo of juice and milkshake bottles" style="left:20px;top:175px;width:130px;height:100px"></div>
    <p class="contact contact--web">info@emberbun.example &nbsp;// &nbsp;www.emberbun.example</p>
    <p class="contact contact--address">Main Road, Building Name, Country</p>
    <div class="social-row"><span></span><span></span><span></span><span></span></div>
  </div>

  <div class="panel">
    <div class="brand"><span class="brand-dot"></span>EMBER BUN CO</div>
    <p class="tagline">It is a good time for the great taste of burgers</p>
    <p class="promo-title promo-title--big">BURGER</p>
    <p class="promo-title promo-title--small">WEEK</p>
    <div class="photo" role="img" aria-label="Photo of burger with fries and a glass of cola" style="left:14px;top:128px;width:136px;height:114px"></div>
    <div class="price-badge"><div class="amount">$5<small>.49</small></div><div class="only">ONLY</div></div>
    <div class="spicy-tag">SPICY AVAILAABLE</div>
    <div class="delivery">
      <svg width="18" height="14" viewBox="0 0 18 14" aria-hidden="true"><rect x="1" y="2" width="9" height="6" fill="none" stroke="#fff" stroke-width="1"/><path d="M10 4h4l3 4v2H10z" fill="none" stroke="#fff" stroke-width="1"/><circle cx="4" cy="11" r="2" fill="none" stroke="#fff"/><circle cx="14" cy="11" r="2" fill="none" stroke="#fff"/></svg>
      <div class="delivery-text"><div class="label">EXPRESS DELIVERY</div><div class="phone">+1 555 014 2270</div></div>
    </div>
  </div>
</section>

<!-- Inside spread -->
<section class="brochure brochure--inside">
  <div class="panel panel--fold-a">
    <div class="photo" role="img" aria-label="Photo of a ketchup bowl" style="left:88px;top:0;width:46px;height:30px;border-radius:0 0 4px 4px"></div>
    <h2 class="menu-heading" style="left:23px;top:33px">BURGERS</h2>
    <ol class="menu-list" style="left:23px;top:51px">
      <li><span class="item-name">Lorem ipsum dolor</span><span class="item-dots"></span><span class="item-price">$10</span></li>
      <li><span class="item-name">Duis aute irure</span><span class="item-dots"></span><span class="item-price">$10</span></li>
      <li><span class="item-name">Excepteur sint occaecat</span><span class="item-dots"></span><span class="item-price">$10</span></li>
      <li><span class="item-name">Consectetur adipiscing elit</span><span class="item-dots"></span><span class="item-price">$10</span></li>
      <li><span class="item-name">Reprehenderit in voluptate</span><span class="item-dots"></span><span class="item-price">$10</span></li>
      <li><span class="item-name">Nostrud exercitation</span><span class="item-dots"></span><span class="item-price">$10</span></li>
      <li><span class="item-name">Ut enim</span><span class="item-dots"></span><span class="item-price">$10</span></li>
      <li><span class="item-name">Spinach artichoke dip</span><span class="item-dots"></span><span class="item-price">$10</span></li>
    </ol>
    <h2 class="menu-heading" style="left:23px;top:193px">BEST BURGERS</h2>
    <ol class="menu-list" style="left:23px;top:211px">
      <li><span class="item-name">Lorem ipsum dolor</span><span class="item-dots"></span><span class="item-price">$10</span></li>
      <li><span class="item-name">Duis aute irure</span><span class="item-dots"></span><span class="item-price">$10</span></li>
      <li><span class="item-name">Excepteur sint occaecat</span><span class="item-dots"></span><span class="item-price">$10</span></li>
      <li><span class="item-name">Consectetur adipiscing elit</span><span class="item-dots"></span><span class="item-price">$10</span></li>
      <li><span class="item-name">Reprehenderit in voluptate</span><span class="item-dots"></span><span class="item-price">$10</span></li>
      <li><span class="item-name">Nostrud exercitation</span><span class="item-dots"></span><span class="item-price">$10</span></li>
      <li><span class="item-name">Ut enim</span><span class="item-dots"></span><span class="item-price">$10</span></li>
      <li><span class="item-name">Spinach artichoke dip</span><span class="item-dots"></span><span class="item-price">$10</span></li>
    </ol>
  </div>

  <div class="panel panel--fold-b">
    <h2 class="menu-heading" style="left:21px;top:33px">CLASIC BURGERS</h2>
    <ol class="menu-list" style="left:21px;top:51px">
      <li><span class="item-name">Lorem ipsum dolor</span><span class="item-dots"></span><span class="item-price">$10</span></li>
      <li><span class="item-name">Duis aute irure</span><span class="item-dots"></span><span class="item-price">$10</span></li>
      <li><span class="item-name">Excepteur sint occaecat</span><span class="item-dots"></span><span class="item-price">$10</span></li>
      <li><span class="item-name">Consectetur adipiscing elit</span><span class="item-dots"></span><span class="item-price">$10</span></li>
      <li><span class="item-name">Reprehenderit in voluptate</span><span class="item-dots"></span><span class="item-price">$10</span></li>
      <li><span class="item-name">Nostrud exercitation</span><span class="item-dots"></span><span class="item-price">$10</span></li>
      <li><span class="item-name">Ut enim</span><span class="item-dots"></span><span class="item-price">$10</span></li>
      <li><span class="item-name">Spinach artichoke dip</span><span class="item-dots"></span><span class="item-price">$10</span></li>
    </ol>
    <h2 class="menu-heading" style="left:21px;top:193px">CLASSIC FRIES</h2>
    <ol class="menu-list" style="left:21px;top:211px">
      <li><span class="item-name">Lorem ipsum dolor</span><span class="item-dots"></span><span class="item-price">$10</span></li>
      <li><span class="item-name">Duis aute irure</span><span class="item-dots"></span><span class="item-price">$10</span></li>
      <li><span class="item-name">Excepteur sint occaecat</span><span class="item-dots"></span><span class="item-price">$10</span></li>
      <li><span class="item-name">Consectetur adipiscing elit</span><span class="item-dots"></span><span class="item-price">$10</span></li>
      <li><span class="item-name">Reprehenderit in voluptate</span><span class="item-dots"></span><span class="item-price">$10</span></li>
      <li><span class="item-name">Nostrud exercitation</span><span class="item-dots"></span><span class="item-price">$10</span></li>
      <li><span class="item-name">Ut enim</span><span class="item-dots"></span><span class="item-price">$10</span></li>
      <li><span class="item-name">Spinach artichoke dip</span><span class="item-dots"></span><span class="item-price">$10</span></li>
    </ol>
    <div class="photo" role="img" aria-label="Photo of a hot sauce bottle" style="left:152px;top:234px;width:17px;height:108px"></div>
  </div>

  <div class="panel">
    <div class="photo" role="img" aria-label="Photo of a sesame burger" style="left:120px;top:0;width:49px;height:52px;border-radius:0 0 0 4px"></div>
    <h2 class="menu-heading" style="left:22px;top:33px">DESSERTS</h2>
    <ol class="menu-list" style="left:22px;top:51px">
      <li><span class="item-name">Lorem ipsum dolor</span><span class="item-dots"></span><span class="item-price">$10</span></li>
      <li><span class="item-name">Duis aute irure</span><span class="item-dots"></span><span class="item-price">$10</span></li>
      <li><span class="item-name">Excepteur sint occaecat</span><span class="item-dots"></span><span class="item-price">$10</span></li>
      <li><span class="item-name">Consectetur adipiscing elit</span><span class="item-dots"></span><span class="item-price">$10</span></li>
      <li><span class="item-name">Reprehenderit in voluptate</span><span class="item-dots"></span><span class="item-price">$10</span></li>
      <li><span class="item-name">Nostrud exercitation</span><span class="item-dots"></span><span class="item-price">$10</span></li>
    </ol>
    <p class="offer-title">SPECIAL OFFER!</p>
    <div class="offer-hours">FROM 2 PM TO 5 PM</div>
    <p class="offer-discount">30% OFF</p>
    <div class="photo" role="img" aria-label="Photo of a plate with burger, fries and ketchup" style="left:27px;top:235px;width:142px;height:120px;border-radius:4px 0 0 0"></div>
  </div>
</section>

</body>
</html>
```